The Plate Compass

Cutting Through the Noise to What Actually Works.

Nutrition book

Target Market(s)

People looking to be or get healthy and eat right.

```html
<!DOCTYPE html>
<html lang="en">
<head>
<meta charset="utf-8">
<title>The Plate Compass – Book Cover</title>
<link rel="stylesheet" href="https://fonts.googleapis.com/css2?family=Literata:opsz,wght@7..72,600;7..72,700&family=Lexend:wght@400&display=swap">
<style>
  :root {
    --backdrop: #8c8c8c;
    --paper: #f7f2e8;
    --paper-glow: #ffffff;
    --ink-dark: #163a27;
    --olive: #6a7f3c;
    --tier-light: #a4b190;
    --tier-mid: #869a78;
    --tier-dark: #3f5a40;
    --tier-line: #b9b4aa;
  }
  * { margin: 0; padding: 0; box-sizing: border-box; }
  html, body {
    width: 1200px; height: 2782px; overflow: hidden;
    background: var(--backdrop);
  }
  .cover {
    position: absolute; left: 60px; top: 581px;
    width: 1080px; height: 1620px;
    background: radial-gradient(ellipse at 50% 52%, var(--paper-glow) 0%, var(--paper) 70%);
    box-shadow: 0 18px 40px rgba(0,0,0,.35);
    text-align: center;
    color: var(--ink-dark);
    font-family: "Literata", Georgia, serif;
  }
  .title { font-weight: 700; }
  .title span {
    position: absolute; left: 0; right: 0;
    display: block; line-height: 1; white-space: nowrap;
  }
  .title-the { top: 123px; font-size: 100px; letter-spacing: -1px; }
  .title-main { top: 208px; font-size: 180px; letter-spacing: -3px; }
  .title-accent { top: 353px; font-size: 180px; letter-spacing: -3px; color: var(--olive); }
  .divider {
    position: absolute; left: 50%; top: 553px; transform: translateX(-50%);
    width: 200px; height: 8px;
    background: radial-gradient(circle, var(--ink-dark) 2.6px, transparent 3px) 0 0 / 18.2px 8px repeat-x;
  }
  .subtitle {
    position: absolute; left: 0; right: 0; top: 600px;
    font-size: 52px; font-weight: 600; line-height: 69px; letter-spacing: .5px;
  }
  .pyramid { position: absolute; left: 0; top: 0; width: 1080px; height: 1620px; }
  .tier-label { font-family: "Lexend", Arial, sans-serif; fill: var(--ink-dark); }
  .tier-outline { fill: #fbf8f2; stroke: var(--tier-line); stroke-width: 1; }
  .author {
    position: absolute; left: 0; right: 0; top: 1440px;
    font-size: 66px; font-weight: 600; line-height: 1; letter-spacing: 2px;
  }
</style>
</head>
<body>
  <main class="cover">
    <h1 class="title">
      <span class="title-the">The</span>
      <span class="title-main">Plate</span>
      <span class="title-accent">Compass</span>
    </h1>
    <div class="divider"></div>
    <p class="subtitle">Cutting Through the Noise<br>to What Actually Works.</p>

    <svg class="pyramid" viewBox="0 0 792 1188" aria-label="Nutrition priority pyramid">
      <defs>
        <linearGradient id="food-tones" x1="0" x2="1">
          <stop offset="0" stop-color="#d86a4c" stop-opacity=".55"/>
          <stop offset=".35" stop-color="#e2c05a" stop-opacity=".6"/>
          <stop offset=".7" stop-color="#5e8a3c" stop-opacity=".6"/>
          <stop offset="1" stop-color="#d9b45a" stop-opacity=".45"/>
        </linearGradient>
      </defs>

      <ellipse cx="402" cy="592" rx="16" ry="8" fill="#4f7a3a" role="img" aria-label="Small leaf sprout atop the pyramid"/>

      <path class="tier-outline" d="M320 656 Q322 609 370 609 L405 609 L405 656 Z"/>
      <path fill="var(--tier-light)" d="M405 609 L430 609 Q471 609 473 656 L405 656 Z"/>
      <rect x="410" y="614" width="40" height="38" rx="4" fill="url(#food-tones)" role="img" aria-label="Photo of junk snacks and candy"/>
      <text class="tier-label" x="365" y="639" font-size="15" text-anchor="middle">Noise</text>

      <path class="tier-outline" d="M274 710 Q276 662 324 662 L431 662 L431 710 Z"/>
      <path fill="var(--tier-light)" d="M431 662 L470 662 Q515 662 517 710 L431 710 Z"/>
      <rect x="435" y="666" width="50" height="40" rx="4" fill="url(#food-tones)" role="img" aria-label="Photo of apple and supplement capsules"/>
      <text class="tier-label" x="354" y="692" font-size="15" text-anchor="middle">Supplements</text>

      <path class="tier-outline" d="M229 766 Q231 716 281 716 L416 716 L416 766 Z"/>
      <path fill="var(--tier-light)" d="M416 716 L508 716 Q559 716 561 766 L416 766 Z"/>
      <rect x="428" y="720" width="90" height="42" rx="4" fill="url(#food-tones)" role="img" aria-label="Photo of a meal bowl and alarm clock"/>
      <text class="tier-label" x="322" y="748" font-size="17" text-anchor="middle">Meal Timing</text>

      <path class="tier-outline" d="M183 828 Q185 772 240 772 L401 772 L401 828 Z"/>
      <path fill="var(--tier-mid)" d="M401 772 L552 772 Q607 772 609 828 L401 828 Z"/>
      <rect x="412" y="776" width="160" height="48" rx="4" fill="url(#food-tones)" role="img" aria-label="Photo of fresh vegetables"/>
      <text class="tier-label" x="292" y="810" font-size="21" text-anchor="middle">Food Quality</text>

      <path class="tier-outline" d="M132 906 Q134 834 204 834 L383 834 L383 906 Z"/>
      <path fill="var(--tier-dark)" d="M383 834 L590 834 Q658 834 660 906 L383 906 Z"/>
      <rect x="395" y="838" width="210" height="64" rx="4" fill="url(#food-tones)" role="img" aria-label="Photo of meat, chicken, nuts and tofu"/>
      <text class="tier-label" x="262" y="884" font-size="32" text-anchor="middle">Protein</text>

      <path class="tier-outline" d="M61 1003 Q63 913 150 913 L339 913 L339 1003 Z"/>
      <path fill="var(--tier-dark)" d="M339 913 L645 913 Q729 913 731 1003 L339 1003 Z"/>
      <rect x="355" y="917" width="290" height="82" rx="4" fill="url(#food-tones)" role="img" aria-label="Photo of fruit, dairy, eggs, greens and oil"/>
      <text class="tier-label" x="207" y="973" font-size="40" text-anchor="middle">Calories</text>
    </svg>

    <p class="author">Marcus Holloway</p>
  </main>
</body>
</html>
```